Harborline Renewal Business Card Design

Professional and clean design. The design colors should flow with the logo. Two-sided card with the website on the back which is:

www.HarborlineRenewal.example.

"Specializing in Water Damage Restoration"

On the front I need the name, email, phone, and logo.

Name: Darnell Quisby
Email: Darnell@HarborlineRenewal.example
Phone: 555-318-2046 for now

I only have the Preview and Thumbnail right now but should have the source files uploaded within a day or two.

Target Market(s)

Flood victims, home owners with water damage from busted pipes etc...

Industry/Entity Type

Business

Contact Information for Business Card

Name: Darnell Quisby

Font styles to use
Serif
Sans Serif

Requirements
Must have
• Business Card Details Info

```html
<!DOCTYPE html>
<html lang="en">
<head>
<meta charset="utf-8">
<title>Harborline Renewal Business Card</title>
<link rel="stylesheet" href="https://fonts.googleapis.com/css2?family=Open+Sans:wght@400;600;700&display=swap">
<style>
  :root {
    --brand-blue: #2a97d4;
    --light-blue: #5cc1ee;
    --paper: #ffffff;
    --backdrop: #e9edf0;
    --ink-white: #ffffff;
  }
  * { margin: 0; padding: 0; box-sizing: border-box; }
  html, body { width: 1200px; height: 900px; overflow: hidden; }
  body {
    background: var(--backdrop);
    font-family: "Open Sans", Arial, sans-serif;
    display: flex;
    flex-direction: column;
    align-items: center;
    justify-content: center;
    gap: 56px;
  }
  .card {
    position: relative;
    width: 640px;
    height: 366px;
    border-radius: 22px;
    overflow: hidden;
    box-shadow: 0 10px 28px rgba(0,0,0,0.18);
  }
  /* Back side */
  .card-back {
    background: var(--brand-blue);
    color: var(--ink-white);
    display: flex;
    flex-direction: column;
    align-items: center;
    padding-top: 58px;
  }
  .back-brand {
    display: flex;
    align-items: center;
    gap: 16px;
  }
  .back-brand .brand-dot {
    width: 110px; height: 110px; border-radius: 50%;
    background: var(--ink-white);
  }
  .back-brand .brand-name {
    font-size: 34px; font-weight: 600; color: var(--ink-white);
    line-height: 1.1; width: 200px;
  }
  .back-tagline {
    margin-top: 62px;
    font-size: 17px; letter-spacing: 0.5px; text-transform: uppercase;
  }
  .back-web { margin-top: 4px; font-size: 17px; }
  /* Front side */
  .card-front { background: var(--paper); }
  .front-shape { position: absolute; inset: 0; }
  .front-contact {
    position: absolute; left: 48px; top: 150px; color: var(--ink-white);
  }
  .front-name {
    font-size: 27px; font-weight: 700; text-transform: uppercase;
    letter-spacing: 0.5px; margin-bottom: 14px;
  }
  .contact-line {
    display: flex; align-items: center; gap: 12px;
    font-size: 17px; line-height: 1.5;
  }
  .contact-line svg { width: 14px; height: 14px; flex: none; }
  .front-brand {
    position: absolute; right: 36px; top: 72px;
    display: flex; flex-direction: column; align-items: center; gap: 12px;
  }
  .front-brand .brand-dot {
    width: 70px; height: 70px; border-radius: 50%; background: var(--brand-blue);
  }
  .front-brand .brand-name {
    font-size: 26px; font-weight: 600; color: var(--brand-blue);
    text-align: center; line-height: 1.15;
  }
</style>
</head>
<body>

<section class="card card-back">
  <div class="back-brand">
    <span class="brand-dot"></span>
    <span class="brand-name">Harborline Renewal</span>
  </div>
  <p class="back-tagline">Specializing in Water Damage Restoration</p>
  <p class="back-web">www.HarborlineRenewal.example</p>
</section>

<section class="card card-front">
  <svg class="front-shape" viewBox="0 0 640 366" preserveAspectRatio="none" aria-hidden="true">
    <path d="M0 0 H360 C440 70 470 230 430 366 H0 Z" fill="var(--brand-blue)"/>
    <path d="M330 0 C430 40 478 200 438 366" fill="none" stroke="var(--brand-blue)" stroke-width="6"/>
    <path d="M350 0 C450 45 492 205 450 366" fill="none" stroke="var(--light-blue)" stroke-width="7"/>
  </svg>

  <div class="front-contact">
    <p class="front-name">Darnell Quisby</p>
    <p class="contact-line">
      <svg viewBox="0 0 16 16"><path d="M3 1.5l3 .5 1 3-2 1.5a9 9 0 0 0 4.5 4.5L11 9l3 1 .5 3-2 1.5C7 14 2 9 1.5 3.5z" fill="currentColor"/></svg>
      555-318-2046
    </p>
    <p class="contact-line">
      <svg viewBox="0 0 16 16"><rect x="1.5" y="3.5" width="13" height="9" fill="none" stroke="currentColor" stroke-width="1.5"/><path d="M1.5 3.5 8 9l6.5-5.5" fill="none" stroke="currentColor" stroke-width="1.5"/></svg>
      Darnell@HarborlineRenewal.example
    </p>
    <p class="contact-line">
      <svg viewBox="0 0 16 16"><circle cx="8" cy="8" r="6.5" fill="none" stroke="currentColor" stroke-width="1.5"/><path d="M1.5 8h13M8 1.5c-3 3.5-3 9.5 0 13M8 1.5c3 3.5 3 9.5 0 13" fill="none" stroke="currentColor" stroke-width="1.2"/></svg>
      www.HarborlineRenewal.example
    </p>
  </div>

  <div class="front-brand">
    <span class="brand-dot"></span>
    <span class="brand-name">Harborline<br>Renewal</span>
  </div>
</section>

</body>
</html>
```